Four in One (Flexible infographic for Content Management Industry)

See attachment.
A graphic depicting 4 products, where each can stand on its own and each can be combined with others, but where, if all are taken together, the best result is achieved (the "super product").
Intended use is web. See attached file as an example.
The most basic idea is as the attached diagram shows, where 4 rectangles are arranged in a quadrangle, with a middle rectangle in the center representing the combined 4 products. This concept is fine except it is a bit too obvious as it stands. We are looking for either a variation of this or another concept.
The audience is technical + professional + enterprise - NOT consumers. Hence the design should be conservative in nature.
We are aware of tools like as Canva or Pictogram where such graphics are available, but we are looking for something with a bit more imagination and flexibility.
This graphic should be targeted to web sites and be delivered with vector-based (SVG) graphics.

```html
<!DOCTYPE html>
<html lang="en">
<head>
<meta charset="utf-8">
<title>Four in One – Super Product</title>
<link rel="stylesheet" href="https://fonts.googleapis.com/css2?family=Roboto:wght@400;500;700&display=swap">
<style>
  :root {
    --backdrop: #3f3f3f;
    --panel: #e7e7e8;
    --card: #ffffff;
    --card-line: #e3e3e3;
    --header: #2e2e2e;
    --ink: #1c1c1c;
    --orange: #f7931e;
    --orange-deep: #f36c0e;
    --green: #8cc63f;
    --green-deep: #6d9a0c;
    --purple: #7b3fc0;
    --purple-deep: #6a2c9f;
    --blue: #1a8cff;
    --blue-deep: #0b4cff;
  }
  * { box-sizing: border-box; margin: 0; padding: 0; }
  html, body { width: 1200px; height: 1200px; overflow: hidden; }
  body {
    background: var(--backdrop);
    font-family: "Roboto", Arial, sans-serif;
    color: var(--ink);
    position: relative;
  }
  .panel {
    position: absolute; left: 61px; top: 196px; width: 1077px; height: 807px;
    background: var(--panel);
  }
  .card {
    position: absolute; width: 454px; height: 311px;
    background: var(--card); border-radius: 50px;
    box-shadow: 0 4px 10px rgba(0,0,0,.18);
  }
  .card.tl { left: 126px; top: 268px; }
  .card.tr { left: 615px; top: 268px; }
  .card.bl { left: 126px; top: 614px; }
  .card.br { left: 615px; top: 614px; }

  .box {
    position: absolute; width: 383px; height: 238px;
    border: 2px solid var(--card-line); border-top: none;
  }
  .tl .box { left: 35px; top: 34px; border-bottom-right-radius: 28px; }
  .tr .box { left: 37px; top: 34px; border-bottom-left-radius: 28px; }
  .bl .box { left: 35px; top: 42px; border-bottom-right-radius: 28px; }
  .br .box { left: 37px; top: 42px; border-bottom-left-radius: 28px; }

  .box-title {
    height: 33px; background: var(--header); color: #fff;
    font-size: 16px; font-weight: 500; line-height: 33px; letter-spacing: .2px;
    padding: 0 35px;
  }
  .tl .box-title { border-top-right-radius: 26px; }
  .bl .box-title { border-top-left-radius: 26px; }
  .tr .box-title { border-top-left-radius: 26px; text-align: right; }
  .br .box-title { border-top-right-radius: 26px; text-align: right; }

  .desc { font-size: 12.4px; line-height: 19.2px; padding: 8px 35px 0; }
  .tr .desc, .br .desc { text-align: right; }

  .features { list-style: none; padding: 11px 35px 0; }
  .features li {
    font-size: 12.6px; font-weight: 700; height: 24px; line-height: 24px;
    display: flex; align-items: center; gap: 12px;
  }
  .tr .features li, .br .features li { justify-content: flex-end; }
  .tick { width: 12px; height: 12px; flex: none; }

  .learn-more {
    display: inline-block; margin: 10px 35px 0; height: 18px; width: 89px;
    border-radius: 9px; color: #fff; font-size: 12.4px; line-height: 18px; text-align: center;
    text-decoration: none;
  }
  .tr .learn-more, .br .learn-more { float: right; }
  .tl .learn-more { background: var(--orange); }
  .tr .learn-more { background: var(--green); }
  .bl .learn-more { background: var(--purple); }
  .br .learn-more { background: var(--blue); }

  .hub { position: absolute; left: 418px; top: 413px; width: 360px; height: 360px; }
  .hub-art {
    position: absolute; left: 518px; top: 517px; width: 162px; height: 102px;
    background: linear-gradient(180deg, #6fa6cf 0%, #5b93c0 70%, #d9dde2 86%, #b7bcc2 100%);
    border-radius: 6px 6px 3px 3px;
  }
  .hub-name {
    position: absolute; left: 500px; top: 626px; width: 200px; text-align: center;
    color: #fff; font-size: 30px; font-weight: 700; line-height: 33px;
  }
</style>
</head>
<body>
  <div class="panel"></div>

  <section class="card tl">
    <div class="box">
      <h2 class="box-title">Document Management</h2>
      <p class="desc">Streamline document organization, access, and<br>collaboration with easier file storage and sharing,<br>leading to more efficient workflows.</p>
      <ul class="features">
        <li><svg class="tick" viewBox="0 0 12 12"><circle cx="6" cy="6" r="6" fill="var(--orange)"/><path d="M3.2 6.2l2 2 3.6-4" stroke="#fff" stroke-width="1.6" fill="none"/></svg>Centralized Document Control</li>
        <li><svg class="tick" viewBox="0 0 12 12"><circle cx="6" cy="6" r="6" fill="var(--orange)"/><path d="M3.2 6.2l2 2 3.6-4" stroke="#fff" stroke-width="1.6" fill="none"/></svg>Collaborative Workspace Integration</li>
        <li><svg class="tick" viewBox="0 0 12 12"><circle cx="6" cy="6" r="6" fill="var(--orange)"/><path d="M3.2 6.2l2 2 3.6-4" stroke="#fff" stroke-width="1.6" fill="none"/></svg>Automated Compliance Tracking</li>
        <li><svg class="tick" viewBox="0 0 12 12"><circle cx="6" cy="6" r="6" fill="var(--orange)"/><path d="M3.2 6.2l2 2 3.6-4" stroke="#fff" stroke-width="1.6" fill="none"/></svg>Check 4</li>
      </ul>
      <a class="learn-more" href="#">Learn More</a>
    </div>
  </section>

  <section class="card tr">
    <div class="box">
      <h2 class="box-title">Security and Compliance</h2>
      <p class="desc">Benefit from tailored cloud solutions, secured data<br>storage, and expert disaster recovery planning for<br>reliable and scalable IT operations.</p>
      <ul class="features">
        <li>Custom Cloud Solutions<svg class="tick" viewBox="0 0 12 12"><circle cx="6" cy="6" r="6" fill="var(--green)"/><path d="M3.2 6.2l2 2 3.6-4" stroke="#fff" stroke-width="1.6" fill="none"/></svg></li>
        <li>Secure Data Storage<svg class="tick" viewBox="0 0 12 12"><circle cx="6" cy="6" r="6" fill="var(--green)"/><path d="M3.2 6.2l2 2 3.6-4" stroke="#fff" stroke-width="1.6" fill="none"/></svg></li>
        <li>Expert Disaster Recovery<svg class="tick" viewBox="0 0 12 12"><circle cx="6" cy="6" r="6" fill="var(--green)"/><path d="M3.2 6.2l2 2 3.6-4" stroke="#fff" stroke-width="1.6" fill="none"/></svg></li>
        <li>Check 4<svg class="tick" viewBox="0 0 12 12"><circle cx="6" cy="6" r="6" fill="var(--green)"/><path d="M3.2 6.2l2 2 3.6-4" stroke="#fff" stroke-width="1.6" fill="none"/></svg></li>
      </ul>
      <a class="learn-more" href="#">Learn More</a>
    </div>
  </section>

  <section class="card bl">
    <div class="box">
      <h2 class="box-title">Enterprise Resource Planning</h2>
      <p class="desc">Simplify management across finance,<br>sales, and operations, enabling better<br>decision-making and improved productivity.</p>
      <ul class="features">
        <li><svg class="tick" viewBox="0 0 12 12"><circle cx="6" cy="6" r="6" fill="var(--purple)"/><path d="M3.2 6.2l2 2 3.6-4" stroke="#fff" stroke-width="1.6" fill="none"/></svg>Integrated Business Processes</li>
        <li><svg class="tick" viewBox="0 0 12 12"><circle cx="6" cy="6" r="6" fill="var(--purple)"/><path d="M3.2 6.2l2 2 3.6-4" stroke="#fff" stroke-width="1.6" fill="none"/></svg>Enhanced Decision-Making</li>
        <li><svg class="tick" viewBox="0 0 12 12"><circle cx="6" cy="6" r="6" fill="var(--purple)"/><path d="M3.2 6.2l2 2 3.6-4" stroke="#fff" stroke-width="1.6" fill="none"/></svg>Productivity Improvement</li>
        <li><svg class="tick" viewBox="0 0 12 12"><circle cx="6" cy="6" r="6" fill="var(--purple)"/><path d="M3.2 6.2l2 2 3.6-4" stroke="#fff" stroke-width="1.6" fill="none"/></svg>Check 4</li>
      </ul>
      <a class="learn-more" href="#">Learn More</a>
    </div>
  </section>

  <section class="card br">
    <div class="box">
      <h2 class="box-title">Digital Transformation</h2>
      <p class="desc">Turn scanned documents into easily<br>searchable digital archives, boosting<br>efficiency and accessibility.</p>
      <ul class="features">
        <li>Instant searchable Archives with OCR<svg class="tick" viewBox="0 0 12 12"><circle cx="6" cy="6" r="6" fill="var(--blue)"/><path d="M3.2 6.2l2 2 3.6-4" stroke="#fff" stroke-width="1.6" fill="none"/></svg></li>
        <li>Automated Document Classification<svg class="tick" viewBox="0 0 12 12"><circle cx="6" cy="6" r="6" fill="var(--blue)"/><path d="M3.2 6.2l2 2 3.6-4" stroke="#fff" stroke-width="1.6" fill="none"/></svg></li>
        <li>ShareHub and Cloud Blob Ready<svg class="tick" viewBox="0 0 12 12"><circle cx="6" cy="6" r="6" fill="var(--blue)"/><path d="M3.2 6.2l2 2 3.6-4" stroke="#fff" stroke-width="1.6" fill="none"/></svg></li>
        <li>Check 4<svg class="tick" viewBox="0 0 12 12"><circle cx="6" cy="6" r="6" fill="var(--blue)"/><path d="M3.2 6.2l2 2 3.6-4" stroke="#fff" stroke-width="1.6" fill="none"/></svg></li>
      </ul>
      <a class="learn-more" href="#">Learn More</a>
    </div>
  </section>

  <svg class="hub" viewBox="-180 -180 360 360">
    <defs>
      <radialGradient id="hub-core" cx="35%" cy="30%" r="80%">
        <stop offset="0" stop-color="#4a4a4a"/>
        <stop offset=".55" stop-color="#121212"/>
        <stop offset="1" stop-color="#000"/>
      </radialGradient>
      <linearGradient id="hub-rim" x1="0" y1="0" x2="1" y2="1">
        <stop offset="0" stop-color="#f4f4f4"/>
        <stop offset=".5" stop-color="#8e8e8e"/>
        <stop offset="1" stop-color="#e2e2e2"/>
      </linearGradient>
    </defs>
    <g class="quadrant-arcs" fill="none" stroke-width="24">
      <path d="M -159 -11 A 159 159 0 0 1 -11 -159" stroke="var(--orange)"/>
      <path d="M 11 -159 A 159 159 0 0 1 159 -11" stroke="var(--green)"/>
      <path d="M -159 11 A 159 159 0 0 0 -11 159" stroke="var(--purple)"/>
      <path d="M 11 159 A 159 159 0 0 0 159 11" stroke="var(--blue)"/>
    </g>
    <circle r="149" fill="url(#hub-rim)"/>
    <circle r="136" fill="url(#hub-core)"/>

    <g class="badge doc" transform="translate(-106 -103)">
      <circle r="44" fill="var(--orange-deep)" stroke="#fff" stroke-width="3"/>
      <path d="M-15 -21h20l10 10v32h-30z" fill="#fff"/>
      <path d="M5 -21v10h10" fill="none" stroke="var(--orange-deep)" stroke-width="2"/>
      <path d="M-9 -4h18M-9 2h18M-9 8h18M-9 14h12" stroke="var(--orange-deep)" stroke-width="2.5"/>
    </g>
    <g class="badge cloud" transform="translate(109 -103)">
      <circle r="44" fill="var(--green-deep)" stroke="#fff" stroke-width="3"/>
      <path d="M-20 8a9 9 0 0 1 2-17a13 13 0 0 1 25-4a11 11 0 0 1 13 21z" fill="#fff"/>
      <path d="M0 -6l11 4v8c0 8-5 13-11 16c-6-3-11-8-11-16v-8z" fill="var(--green-deep)" stroke="#fff" stroke-width="2"/>
      <path d="M-5 4l4 4 7-8" fill="none" stroke="#fff" stroke-width="2.5"/>
    </g>
    <g class="badge chart" transform="translate(-106 104)">
      <circle r="44" fill="var(--purple-deep)" stroke="#fff" stroke-width="3"/>
      <rect x="-18" y="-17" width="36" height="34" fill="none" stroke="#fff" stroke-width="2.5"/>
      <path d="M-8 12v-12M0 12v-20M8 12v-8" stroke="#fff" stroke-width="5"/>
      <g fill="#fff"><circle cx="-18" cy="-17" r="4"/><circle cx="18" cy="-17" r="4"/><circle cx="-18" cy="17" r="4"/><circle cx="18" cy="17" r="4"/></g>
    </g>
    <g class="badge gear" transform="translate(109 104)">
      <circle r="44" fill="var(--blue-deep)" stroke="#fff" stroke-width="3"/>
      <path d="M2 -18a18 18 0 1 0 0 36" fill="none" stroke="#fff" stroke-width="7" stroke-dasharray="6 3"/>
      <path d="M2 -9a9 9 0 1 0 0 18" fill="none" stroke="#fff" stroke-width="3"/>
      <path d="M6 -12h8M6 -4h12M6 4h12M6 12h8" stroke="#fff" stroke-width="2.5"/>
      <g fill="#fff"><circle cx="15" cy="-12" r="3"/><circle cx="19" cy="-4" r="3"/><circle cx="19" cy="4" r="3"/><circle cx="15" cy="12" r="3"/></g>
    </g>
  </svg>

  <div class="hub-art" role="img" aria-label="Illustration of a laptop with a thumbs-up on its screen"></div>
  <p class="hub-name">Super<br>Product</p>
</body>
</html>
```